Elegant Business Card for Technology Company

Client is a supplier of innovative industrial communications and automation equipment since 2002. This contest is to gather fresh ideas for a redesign of the existing business card. Client is looking for design that best communicates tagline "Industrial Networking and Computing Specialist".

Design submissions should look modern, clean, elegant and professional. It should not be cluttered. Use white as the primary colour. Orange and black as secondary colour. Refer to jpeg File 1 on the current design.

Fonts used by Client used include Arial Regular, Arial Black, Roboto Regular, Roboto Black and Lato.

The winning design will be sent for offset printing using super white 250gsm artcard paper (open for suggestions).

Target Market(s)

System Engineers, Project Managers, Purchasing Managers from companies providing engineering services for Smart Cities.

Industry/Entity Type

Information Technology

Contact Information for Business Card

Refer to PDF File 3 for Business Card Details. Priority of short contact information would be as follows Name > Job Title > Email > Mobile > Web > Tel > Fax > Business Address >UEN (UEN represents company registration number)

Font styles to use
Sans Serif

Colors
ffffff
f37122
000000
5c5c5c

Requirements
Must have
• Refer to AI File 2 (Company Logo) & PDF File 3 (Information on Namecard)
Should not have
• No QR codes
• No Social Media Icons
• Do not create full Black or Orange colour background

```html
<!DOCTYPE html>
<html lang="en">
<head>
<meta charset="utf-8">
<title>Norvex Business Card</title>
<link href="https://fonts.googleapis.com/css2?family=Arimo:wght@400;700&display=swap" rel="stylesheet">
<style>
  :root {
    --ink: #000000;
    --paper: #ffffff;
    --orange: #f37122;
    --grey: #5c5c5c;
    --rule: #bdbdbd;
    --backdrop: #3a3a3a;
  }
  * { margin: 0; padding: 0; box-sizing: border-box; }
  html, body { width: 1200px; height: 900px; overflow: hidden; }
  body {
    background: var(--backdrop);
    font-family: "Arimo", Arial, sans-serif;
    color: var(--ink);
    position: relative;
  }
  .card {
    position: absolute;
    left: 250px;
    width: 700px;
    height: 400px;
    background: var(--paper);
    box-shadow: 0 10px 30px rgba(0,0,0,.55);
    overflow: hidden;
  }
  .card--front { top: 40px; }
  .card--back { top: 460px; }

  .brand {
    position: absolute;
    display: flex;
    align-items: center;
    gap: 14px;
  }
  .brand__dot {
    border-radius: 50%;
    background: var(--orange);
    flex: none;
  }
  .brand__name {
    font-weight: 700;
    color: var(--ink);
    letter-spacing: 1px;
    white-space: nowrap;
  }

  /* Front */
  .card--front .brand { left: 330px; top: 58px; }
  .card--front .brand__dot { width: 84px; height: 84px; }
  .card--front .brand__name { font-size: 54px; }
  .tagline {
    position: absolute;
    right: 150px;
    top: 162px;
    color: var(--orange);
    font-size: 15px;
    letter-spacing: .3px;
    text-transform: uppercase;
    white-space: nowrap;
  }
  .services {
    position: absolute;
    left: 190px;
    top: 236px;
    list-style: none;
    font-size: 16px;
    line-height: 23px;
    color: var(--ink);
  }
  .services li { position: relative; padding-left: 24px; white-space: nowrap; }
  .services li::before {
    content: "";
    position: absolute;
    left: 0; top: 7px;
    width: 10px; height: 10px;
    border-radius: 50%;
    background: var(--orange);
  }

  /* Back */
  .card--back .brand { left: 50px; top: 48px; }
  .card--back .brand__dot { width: 72px; height: 72px; }
  .card--back .brand__name { font-size: 46px; }
  .company {
    position: absolute;
    left: 50px;
    top: 144px;
    font-size: 16px;
    letter-spacing: .4px;
    color: var(--grey);
    white-space: nowrap;
  }
  .company__lead { color: var(--orange); font-weight: 700; }
  .divider {
    position: absolute;
    left: 50px;
    right: 36px;
    top: 184px;
    height: 1px;
    background: var(--rule);
  }
  .contacts {
    position: absolute;
    left: 50px;
    top: 212px;
    list-style: none;
    font-size: 16px;
    line-height: 27px;
    color: var(--ink);
  }
  .contacts li { display: flex; align-items: center; gap: 12px; white-space: nowrap; }
  .contacts svg { width: 14px; height: 14px; flex: none; }

  .person {
    position: absolute;
    right: 36px;
    top: 120px;
    text-align: right;
  }
  .person__name { font-size: 24px; font-weight: 700; letter-spacing: .5px; color: var(--ink); line-height: 26px; }
  .person__title { font-size: 15px; color: var(--orange); letter-spacing: .8px; line-height: 20px; }
  .person-tab {
    position: absolute;
    right: 0;
    top: 120px;
    width: 22px;
    height: 46px;
    background: var(--orange);
  }
  .uen {
    position: absolute;
    right: 36px;
    top: 204px;
    background: var(--orange);
    color: var(--paper);
    font-size: 15px;
    padding: 4px 12px;
    white-space: nowrap;
  }
  .address {
    position: absolute;
    right: 36px;
    top: 250px;
    text-align: right;
    font-size: 15px;
    line-height: 21px;
    color: var(--grey);
    white-space: nowrap;
  }
</style>
</head>
<body>

<section class="card card--front" aria-label="Card front">
  <div class="brand">
    <span class="brand__dot"></span>
    <span class="brand__name">NORVEX</span>
  </div>
  <p class="tagline">Industrial Networking and Computing Specialist</p>
  <ul class="services">
    <li>Industrial Ethernet / Wireless / Cellular</li>
    <li>Industrial and Embedded Computing</li>
    <li>Serial / Fieldbus Connectivity</li>
    <li>IP Video Surveillance</li>
    <li>Remote Automation</li>
  </ul>
</section>

<section class="card card--back" aria-label="Card back">
  <div class="brand">
    <span class="brand__dot"></span>
    <span class="brand__name">NORVEX</span>
  </div>
  <p class="company"><span class="company__lead">NORVEX</span> ASIA PACIFIC PTE LTD</p>
  <div class="divider"></div>

  <ul class="contacts">
    <li>
      <svg viewBox="0 0 14 14"><rect x="3.5" y="1" width="7" height="12" rx="1.2" fill="none" stroke="#f37122" stroke-width="1.4"/><circle cx="7" cy="11" r=".8" fill="#f37122"/></svg>
      +65 8123 4567
    </li>
    <li>
      <svg viewBox="0 0 14 14"><path d="M3 1.5l2.2 0 1 3-1.4 1.2a7 7 0 0 0 3.5 3.5l1.2-1.4 3 1v2.2a1.2 1.2 0 0 1-1.3 1.2A11 11 0 0 1 1.8 2.8 1.2 1.2 0 0 1 3 1.5z" fill="#f37122"/></svg>
      +65 6555 0140
    </li>
    <li>
      <svg viewBox="0 0 14 14"><rect x="3.5" y="1" width="7" height="4" fill="#f37122"/><rect x="1" y="5.5" width="12" height="5" rx="1" fill="#f37122"/><rect x="3.5" y="9" width="7" height="4" fill="#f37122"/></svg>
      +65 6555 0183
    </li>
    <li>
      <svg viewBox="0 0 14 14"><rect x="1" y="3" width="12" height="8.5" fill="none" stroke="#f37122" stroke-width="1.4"/><path d="M1 3l6 5 6-5" fill="none" stroke="#f37122" stroke-width="1.4"/></svg>
      sales@norvex.com.sg
    </li>
    <li>
      <svg viewBox="0 0 14 14"><circle cx="7" cy="7" r="6" fill="#f37122"/><path d="M1 7h12M7 1c-2.5 3-2.5 9 0 12M7 1c2.5 3 2.5 9 0 12" fill="none" stroke="#ffffff" stroke-width="1"/></svg>
      www.norvex.com.sg
    </li>
  </ul>

  <div class="person-tab"></div>
  <div class="person">
    <p class="person__name">DANIEL KOH</p>
    <p class="person__title">SALES MANAGER</p>
  </div>
  <p class="uen">UEN No: 201804417K</p>
  <p class="address">21 Kallang Vista Techhub #04-12<br>(Block B), Singapore 339712</p>
</section>

</body>
</html>
```